Brivo Australia Dental

I need to update my website and design. I have some ideas in mind and would like to replicate the format from another website into my own. I need the website to be easy to edit (I have no prior wordpress exp) after the design is complete. Please visit https://thelittlenestcare.org.au/ for example of layout.
Target Market(s)
Parents and elder folks
Industry/Entity Type
Dental
Coding
Coded - Design and coding required
Number of Pages Required
4 page
Font styles to use
Sans Serif
Colors
0392cd
Requirements
Must have
- - Home, Services, About Us, News
- - Colours
- - Clear action from viewers
- - Location of business (able to change all the time)
- - Illustrations/ photos

```html
<!DOCTYPE html>
<html lang="en">
<head>
<meta charset="utf-8">
<title>Brivo Australia Dental</title>
<link href="https://fonts.googleapis.com/css2?family=Open+Sans:wght@400;600;700&display=swap" rel="stylesheet">
<style>
:root{
  --blue:#1780c6;
  --ink:#222;
  --text:#333;
  --pale:#dfe9ee;
  --grey:#e4e4e6;
  --black:#000;
  --white:#fff;
}
*{box-sizing:border-box;margin:0;padding:0}
html,body{width:1200px;height:3810px;overflow:hidden}
body{position:relative;font-family:"Open Sans",Arial,sans-serif;color:var(--text);background:var(--white)}
.abs{position:absolute}
.btn{position:absolute;background:var(--blue);color:var(--white);font-weight:600;font-size:15px;display:flex;align-items:center;justify-content:center;text-transform:uppercase}
.section-title{position:absolute;font-size:30px;font-weight:400;color:var(--ink);letter-spacing:.5px;display:flex;align-items:center;white-space:nowrap}
.section-title::after{content:"";display:inline-block;width:80px;height:3px;background:var(--blue);margin-left:18px}
.photo{position:absolute}

/* header */
.site-header{position:absolute;left:0;top:0;width:1200px;height:103px;background:#f2f2f3}
.brand{position:absolute;left:111px;top:16px;color:var(--blue);font-size:40px;font-weight:400;line-height:1}
.brand-tag{position:absolute;left:112px;top:72px;color:var(--blue);font-size:11px;letter-spacing:2px}
.call{position:absolute;left:724px;top:22px;font-size:16px;color:var(--ink)}
.call b{font-size:20px;font-weight:700}
.signup{left:977px;top:13px;width:110px;height:39px;font-size:15px}
.nav{position:absolute;top:70px;left:0;width:1200px;font-size:19px;color:var(--ink)}
.nav span{position:absolute}
.nav .active{color:var(--blue);border-bottom:3px solid var(--blue);padding:0 2px 6px}

/* hero */
.hero{position:absolute;left:0;top:103px;width:1200px;height:617px;
  background:
    linear-gradient(90deg,rgba(30,26,24,.55) 0%,rgba(30,26,24,.15) 45%,rgba(0,0,0,0) 60%),
    radial-gradient(ellipse 170px 200px at 510px 250px,#d8ae94 0%,rgba(216,174,148,0) 100%),
    radial-gradient(ellipse 260px 240px at 180px 120px,#4a372d 0%,rgba(74,55,45,0) 100%),
    radial-gradient(ellipse 320px 170px at 560px 560px,#b9c47a 0%,rgba(185,196,122,0) 100%),
    radial-gradient(ellipse 180px 150px at 820px 500px,#7fa8cc 0%,rgba(127,168,204,0) 100%),
    radial-gradient(ellipse 260px 300px at 1000px 220px,#d9dfe3 0%,rgba(217,223,227,0) 100%),
    linear-gradient(90deg,#5a4c44 0%,#8c7b70 40%,#a9a6a2 70%,#cfd4d7 100%)}
.hero h1{position:absolute;left:111px;top:252px;font-size:52px;font-weight:600;color:var(--white);letter-spacing:1px}
.hero h2{position:absolute;left:111px;top:320px;font-size:31px;font-weight:600;color:var(--white)}
.hero-btn{left:111px;top:374px;width:184px;height:56px}
.arrow{position:absolute;top:341px;width:38px;height:38px;border-radius:50%;background:var(--white)}

/* about */
.about-text{position:absolute;left:111px;top:866px;width:446px;font-size:15.5px;line-height:30px;text-align:justify;color:var(--ink)}

/* services */
.services{position:absolute;left:0;top:1340px;width:1200px;height:390px;background:linear-gradient(135deg,#e4eef2,#d6e4ea 50%,#e2ecf0)}
.pill{position:absolute;top:138px;width:468px;height:184px;background:var(--blue);border-radius:92px;color:var(--white)}
.pill .thumb{position:absolute;left:2px;top:16px;width:144px;height:144px;border-radius:50%}
.pill h3{position:absolute;left:172px;top:32px;font-size:14.5px;font-weight:600}
.pill p{position:absolute;left:172px;top:56px;width:250px;font-size:14.5px;line-height:20px}
.pill .more{position:absolute;left:174px;top:128px;font-size:14.5px;font-weight:600;display:flex;align-items:center;gap:6px}

/* different */
.card{position:absolute;top:1921px;width:313px;height:431px;background:var(--white);box-shadow:0 2px 6px rgba(0,0,0,.18)}
.card .pic{position:absolute;left:0;top:0;width:313px;height:248px}
.card h3{position:absolute;left:0;top:274px;width:100%;text-align:center;font-size:18px;font-weight:400;color:var(--ink)}
.card p{position:absolute;left:26px;top:306px;width:261px;text-align:center;font-size:18px;line-height:27px;color:var(--ink)}
.card-btn{left:83px;top:402px;width:148px;height:41px;font-size:15px}

/* contact */
.contact{position:absolute;left:0;top:2488px;width:1200px;height:516px;background:var(--blue)}
.contact h2{position:absolute;left:670px;top:48px;font-size:34px;font-weight:400;color:var(--white)}
.field{position:absolute;left:673px;width:432px;background:var(--white);font-size:16px;color:var(--ink);padding:12px 15px}
.submit{position:absolute;left:673px;top:412px;width:432px;height:45px;background:var(--white);color:var(--ink);font-size:16px;font-weight:600;display:flex;align-items:center;justify-content:center}

/* info */
.info{position:absolute;left:0;top:3004px;width:1200px;height:483px;background:radial-gradient(ellipse 500px 300px at 200px 300px,#f1f1f3,#dcdcdf)}
.info h4{position:absolute;font-size:22px;font-weight:400;color:var(--ink)}
.info p{position:absolute;font-size:16px;line-height:23px;color:var(--ink)}
.map{position:absolute;left:520px;top:55px;width:566px;height:371px;
  background:
    radial-gradient(ellipse 120px 200px at 290px 220px,#f6efd2 0%,rgba(246,239,210,0) 100%),
    radial-gradient(ellipse 200px 120px at 470px 80px,#e3eee0 0%,rgba(227,238,224,0) 100%),
    radial-gradient(ellipse 160px 140px at 300px 210px,#f1e3e3 0%,rgba(241,227,227,0) 100%),
    linear-gradient(135deg,#f3f3f3,#e6e8ea);box-shadow:0 1px 4px rgba(0,0,0,.15)}
.map-card{position:absolute;left:520px;top:55px;width:288px;height:108px;background:var(--white);box-shadow:0 1px 4px rgba(0,0,0,.2);padding:22px 16px;font-size:15px;line-height:23px;color:var(--ink);white-space:nowrap}

/* footer */
.footer{position:absolute;left:0;top:3487px;width:1200px;height:323px;background:var(--black);color:var(--white)}
.footer h5{position:absolute;font-size:15.5px;font-weight:400}
.footer .links{position:absolute;left:229px;top:117px;font-size:16px;font-weight:600;line-height:30px}
.footer .row{position:absolute;left:467px;font-size:16px;line-height:22px;display:flex;gap:10px}
.footer .hours{position:absolute;left:867px;top:116px;font-size:16px;line-height:27px}
.social{position:absolute;top:3703px;width:24px;height:24px;border:2px solid var(--white);border-radius:50%}
.copy{position:absolute;left:467px;top:3774px;font-size:16px;color:var(--white)}
</style>
</head>
<body>

<header class="site-header">
  <div class="brand">Brivo</div>
  <div class="brand-tag">for a better smile</div>
  <div class="call">CALL NOW : <b>1300 555 204</b></div>
  <div class="btn signup">Sign Up</div>
  <nav class="nav">
    <span class="active" style="left:498px">Home</span>
    <span style="left:611px">Services</span>
    <span style="left:742px">About Us</span>
    <span style="left:884px">News</span>
    <span style="left:990px">Contact us</span>
  </nav>
</header>

<section class="hero" role="img" aria-label="Smiling child at a dental check-up with a dentist">
  <div class="arrow" style="left:25px"><svg width="38" height="38"><path d="M22 12 L15 19 L22 26" fill="none" stroke="#333" stroke-width="1.8"/></svg></div>
  <div class="arrow" style="left:1123px"><svg width="38" height="38"><path d="M16 12 L23 19 L16 26" fill="none" stroke="#333" stroke-width="1.8"/></svg></div>
  <h1>BRIVO AUSTRALIA</h1>
  <h2>FOR A BETTER SMILE</h2>
  <div class="btn hero-btn">Get Started</div>
</section>

<h2 class="section-title" style="left:111px;top:812px">ABOUT US</h2>
<p class="about-text">Brivo Mobile Dental is a group of Dental Professionals who strongly believes anyone and anywhere can look healthy and fabulous with a bright Smile.Our work is our purpose, our driving force. Our patients are our number one priority and we will help you through all your Dental needs.Our actions do the talking. Our caring and passionate staff will meet all your dental needs to ensure you are comfortable during the procedure and leave our clinic with a Smile. Our purpose is to Educate anyone and everyone how to create and maintain their best Smile possible.</p>
<div class="btn" style="left:111px;top:1185px;width:172px;height:52px">Read More</div>
<div class="photo" role="img" aria-label="Modern dental chair in a bright clinic room" style="left:615px;top:822px;width:474px;height:415px;background:
  radial-gradient(ellipse 120px 200px at 60px 260px,#8d8680 0%,rgba(141,134,128,0) 100%),
  radial-gradient(ellipse 160px 90px at 420px 400px,#2a2a2c 0%,rgba(42,42,44,0) 100%),
  radial-gradient(ellipse 200px 160px at 300px 200px,#b9c2c9 0%,rgba(185,194,201,0) 100%),
  linear-gradient(135deg,#f5f7f9,#e3e8ec 50%,#c8d0d6)"></div>

<section class="services">
  <h2 class="section-title" style="left:438px;top:52px">OUR SERVICES</h2>
  <div class="pill" style="left:111px">
    <div class="thumb" role="img" aria-label="Children's drawings and coloured pencils" style="background:
      radial-gradient(circle at 70% 60%,#e9e6df 0%,rgba(233,230,223,0) 55%),
      radial-gradient(circle at 35% 75%,#3f8f5a 0%,rgba(63,143,90,0) 40%),
      radial-gradient(circle at 60% 85%,#d04a3a 0%,rgba(208,74,58,0) 35%),
      linear-gradient(160deg,#2d3440,#6c7076 50%,#b9b4aa)"></div>
    <h3>GROW TO SMILE PROGRAM</h3>
    <p>Our mobile performed within the spacious compounds of our State of the Art Mobile clinic</p>
    <div class="more">READ MORE <svg width="15" height="15"><circle cx="7.5" cy="7.5" r="6.5" fill="none" stroke="#fff" stroke-width="1.3"/><path d="M6 4.5 L9 7.5 L6 10.5" fill="none" stroke="#fff" stroke-width="1.3"/></svg></div>
  </div>
  <div class="pill" style="left:618px">
    <div class="thumb" role="img" aria-label="Soft cushions and blankets in a calm room" style="background:
      radial-gradient(circle at 60% 60%,#8a7f72 0%,rgba(138,127,114,0) 45%),
      radial-gradient(circle at 30% 30%,#f3efe8 0%,rgba(243,239,232,0) 60%),
      linear-gradient(135deg,#ddd6cb,#a79d90)"></div>
    <h3>BEAUTIFUL &amp; RETIRED PROGRAM</h3>
    <p style="text-align:justify">Beautiful &amp; Retired" Program is designed by dental professionals aimed to educate methods</p>
    <div class="more">READ MORE <svg width="15" height="15"><circle cx="7.5" cy="7.5" r="6.5" fill="none" stroke="#fff" stroke-width="1.3"/><path d="M6 4.5 L9 7.5 L6 10.5" fill="none" stroke="#fff" stroke-width="1.3"/></svg></div>
  </div>
</section>

<h2 class="section-title" style="left:339px;top:1825px">WHAT MAKES US DIFFERENT</h2>
<article class="card" style="left:111px">
  <div class="pic" role="img" aria-label="Dental treatment room with equipment" style="background:
    radial-gradient(ellipse 60px 140px at 10px 200px,#8a837d 0%,rgba(138,131,125,0) 100%),
    radial-gradient(ellipse 110px 90px at 260px 130px,#aeb6bd 0%,rgba(174,182,189,0) 100%),
    linear-gradient(135deg,#f6f8fa,#dde3e8)"></div>
  <h3>OUR STORY</h3>
  <p>Dr Maren Holt and her team beautiful Smile, whoever and where ever you may be.</p>
</article>
<article class="card" style="left:441px;height:465px">
  <div class="pic" role="img" aria-label="Close-up of a dental chair and instruments" style="background:
    radial-gradient(ellipse 160px 120px at 170px 150px,#f0f0f0 0%,rgba(240,240,240,0) 100%),
    radial-gradient(ellipse 120px 70px at 90px 20px,#7a604c 0%,rgba(122,96,76,0) 100%),
    radial-gradient(ellipse 80px 160px at 30px 170px,#5c5a58 0%,rgba(92,90,88,0) 100%),
    linear-gradient(135deg,#8d7766,#c9c7c4 50%,#8f8f90)"></div>
  <h3>OUR MISSION</h3>
  <p>At Brivo we aim to put a Smile on your face. Our dedicated the best</p>
  <div class="btn card-btn">Read More</div>
</article>
<article class="card" style="left:771px">
  <div class="pic" role="img" aria-label="Three smiling members of the dental team" style="background:
    radial-gradient(ellipse 70px 90px at 70px 90px,#b9775a 0%,rgba(185,119,90,0) 100%),
    radial-gradient(ellipse 60px 70px at 155px 60px,#d9b49c 0%,rgba(217,180,156,0) 100%),
    radial-gradient(ellipse 80px 110px at 270px 200px,#1f9a8a 0%,rgba(31,154,138,0) 100%),
    radial-gradient(ellipse 90px 120px at 160px 200px,#f4f6f7 0%,rgba(244,246,247,0) 100%),
    linear-gradient(90deg,#e6e3df,#d8d5d1 55%,#b9c6c4)"></div>
  <h3>OUR TEAM</h3>
  <p>At Brivo, our team consists of qualified and Therapists experience</p>
</article>

<section class="contact">
  <svg class="abs" style="left:0;top:0" width="640" height="516" role="img" aria-label="Smiling dental therapist with a young patient">
    <defs>
      <linearGradient id="cbase" x1="0" x2="1" y1="0" y2="1"><stop offset="0" stop-color="#c9ccce"/><stop offset=".45" stop-color="#8e9297"/><stop offset="1" stop-color="#3a3f48"/></linearGradient>
      <radialGradient id="skinA" cx=".5" cy=".5" r=".5"><stop offset="0" stop-color="#c8967a"/><stop offset="1" stop-color="#c8967a" stop-opacity="0"/></radialGradient>
      <radialGradient id="navy" cx=".5" cy=".5" r=".5"><stop offset="0" stop-color="#1f2d5a"/><stop offset="1" stop-color="#1f2d5a" stop-opacity="0"/></radialGradient>
      <radialGradient id="jacket" cx=".5" cy=".5" r=".5"><stop offset="0" stop-color="#1b1c20"/><stop offset="1" stop-color="#1b1c20" stop-opacity="0"/></radialGradient>
      <radialGradient id="amber" cx=".5" cy=".5" r=".5"><stop offset="0" stop-color="#e2a43a"/><stop offset="1" stop-color="#e2a43a" stop-opacity="0"/></radialGradient>
      <clipPath id="cclip"><polygon points="0,0 640,0 525,516 0,516"/></clipPath>
    </defs>
    <g clip-path="url(#cclip)">
      <rect width="640" height="516" fill="url(#cbase)"/>
      <ellipse cx="120" cy="400" rx="200" ry="200" fill="url(#navy)"/>
      <ellipse cx="390" cy="440" rx="220" ry="160" fill="url(#jacket)"/>
      <ellipse cx="520" cy="330" rx="90" ry="150" fill="url(#amber)"/>
      <ellipse cx="130" cy="150" rx="110" ry="130" fill="url(#skinA)"/>
      <ellipse cx="370" cy="190" rx="110" ry="120" fill="url(#skinA)"/>
    </g>
  </svg>
  <h2>CONTACT US</h2>
  <div class="field" style="top:118px;height:45px">Name</div>
  <div class="field" style="top:177px;height:45px">Email</div>
  <div class="field" style="top:231px;height:45px">Phone</div>
  <div class="field" style="top:288px;height:115px">Message</div>
  <div class="submit">SUBMIT</div>
</section>

<section class="info">
  <h4 style="left:161px;top:102px">CONTACT</h4>
  <p style="left:161px;top:135px;font-size:21px;font-weight:600">1300 555 204</p>
  <h4 style="left:164px;top:188px">ADDRESS</h4>
  <p style="left:161px;top:221px">HILLVIEW PUBLIC SCHOOL<br>42 CARTER STREET, HILLVIEW NSW 2590</p>
  <h4 style="left:161px;top:293px">OPENING HOURS</h4>
  <p style="left:161px;top:327px">Mon: 8AM to 4PM<br>Thurs: 8AM to 4PM<br>Fri: 8AM to 4PM</p>
  <div class="map" role="img" aria-label="Street map showing the clinic location"></div>
  <div class="map-card">Hillview Public School<br>42 Carter Street, Hillview NSW 2590</div>
</section>

<footer class="footer">
  <h5 style="left:229px;top:72px">QUICKLINKS</h5>
  <div class="links">Home<br>Services<br>About Us<br>News<br>Contact us</div>
  <h5 style="left:467px;top:72px">CONTACT</h5>
  <div class="row" style="top:118px"><svg width="18" height="18"><path d="M4 2 L7 2 L8 6 L6 7.5 Q8 11 10.5 12 L12 10 L16 11 L16 14 Q15 16 12 15.5 Q4 13 2.5 5 Q2.5 2.5 4 2Z" fill="none" stroke="#fff" stroke-width="1.2"/></svg><span style="font-weight:600">1300 555 204</span></div>
  <div class="row" style="top:153px"><svg width="18" height="18"><path d="M9 17 Q3 10 3 7 A6 6 0 0 1 15 7 Q15 10 9 17Z" fill="#fff"/><circle cx="9" cy="7" r="2.2" fill="#000"/></svg><span>Hillview Public School<br>42 Carter Street, Hillview NSW 2590</span></div>
  <div class="row" style="top:213px"><svg width="18" height="18"><rect x="2" y="4" width="14" height="10" fill="none" stroke="#fff" stroke-width="1.2"/><path d="M2 4 L9 10 L16 4" fill="none" stroke="#fff" stroke-width="1.2"/></svg><span>hello@brivodental.com.au</span></div>
  <h5 style="left:864px;top:76px">OPENING HOURS</h5>
  <div class="hours">Mon: 8AM to 4PM<br>Thurs: 8AM to 4PM<br>Fri: 8AM to 4PM</div>
</footer>
<div class="social" style="left:871px"></div>
<div class="social" style="left:899px"></div>
<div class="social" style="left:927px"></div>
<div class="social" style="left:955px"></div>
<div class="copy">Copyrights © 2019 All Rights Reserved</div>

</body>
</html>
```